web page design with coding

We are a start up insurance agency who needs to design a full functional web page. we recently did a postcard design though drawkettle I will upload the final project for you to see the color scheme/font we would like to continue to use. I also have a rough draft of verbage I would like our website to have. I will upload that as well.

Reason: I am sorry but the person who will make the final decision on the website is out of the country at the moment and will make the final decision when he returns.

Industry/Entity Type

Insurance

Coding

Coded - Design and coding required

```html
<!DOCTYPE html>
<html lang="en">
<head>
<meta charset="utf-8">
<title>Harbora Insurance Group</title>
<link href="https://fonts.googleapis.com/css2?family=Open+Sans:wght@300;400;600&display=swap" rel="stylesheet">
<style>
:root{
  --navy:#1b3f6e;
  --blue-left:#1f4c86;
  --gold:#f2c34e;
  --green:#3f8a3a;
  --text:#333;
  --muted:#777;
  --light:#ececec;
  --footer:#3b3b3b;
  --footer-line:#555;
  --white:#fff;
}
*{box-sizing:border-box;margin:0;padding:0}
html,body{width:747px;height:1200px;overflow:hidden}
body{font-family:"Open Sans",Arial,sans-serif;background:var(--white);color:var(--text);position:relative}
.abs{position:absolute}

.brand{left:83px;top:26px;display:flex;align-items:center;gap:7px;font-size:16px;font-weight:400;color:var(--navy)}
.brand .mark{width:12px;height:12px;background:var(--navy)}
.top-phone{right:77px;top:17px;font-size:10.4px;color:var(--navy);display:flex;align-items:center;gap:5px}
.nav{right:77px;top:44px;display:flex;gap:19px;font-size:7.4px;color:#777}
.nav .active{color:var(--green)}

.hero{left:0;top:70px;width:747px;height:252px;background:linear-gradient(100deg,#d9d6d2 0%,#ece9e6 40%,#f3f1ef 70%,#e6eaee 100%)}
.dots{left:349px;top:295px;width:48px;height:11px;border-radius:6px;background:#8d8d8d;display:flex;justify-content:center;align-items:center;gap:5px}
.dots span{width:5px;height:5px;border-radius:50%;background:#eee}
.dots span.on{background:none;border:1px solid #eee}

.welcome{left:82px;top:345px;width:583px;text-align:center}
.welcome h1{font-weight:400;font-size:21px;line-height:26px;color:var(--navy)}
.welcome .lead{font-size:8px;font-weight:400;color:#222;margin-top:8px}
.welcome p.body{font-size:5.9px;color:var(--muted);line-height:12px;margin-top:8px}

.band{top:491px;height:250px}
.band.left{left:0;width:426px;background:var(--blue-left)}
.band.right{left:426px;width:321px;background:linear-gradient(160deg,#2d5d99,#234f8a)}
.band h2{position:absolute;top:16px;font-weight:400;font-size:20px;color:var(--gold)}
.band ul{position:absolute;top:51px;list-style:none;font-size:6.2px;color:var(--white)}
.band li{height:16.9px}
.band li::before{content:"•";margin-right:4px}

.quote{left:0;top:741px;width:747px;height:188px;background:var(--light)}
.quote h2{position:absolute;top:19px;width:100%;text-align:center;font-weight:400;font-size:19px;color:var(--navy)}
.field{position:absolute;height:25px;background:var(--white);border:1px solid #ddd;font-size:6.2px;color:#666;padding:0 10px;display:flex;align-items:center}
.field .arrow{margin-left:auto;border-left:1px solid #ccc;padding-left:5px;font-size:5px}
.btn-next{left:345px;top:135px;width:57px;height:24px;background:#3d3d3d;color:var(--white);font-size:7px;display:flex;align-items:center;justify-content:center}

.map{left:0;top:929px;width:747px;height:154px;background:linear-gradient(180deg,#e4e4e4,#d8d8d8)}

.footer{left:0;top:1083px;width:747px;height:117px;background:var(--footer);color:#ddd;font-size:6.6px}
.info{position:absolute;top:21px;display:flex;gap:5px;align-items:flex-start;line-height:11px;white-space:nowrap}
.social{position:absolute;left:550px;top:16px;display:flex;gap:6px}
.social span{width:24px;height:24px;border-radius:50%;background:var(--white)}
.rule{position:absolute;left:0;top:57px;width:747px;height:1px;background:var(--footer-line)}
.links{position:absolute;left:83px;top:74px;font-size:6.2px}
.copy{position:absolute;left:83px;top:92px;font-size:6.2px}
.btn-contact{position:absolute;left:585px;top:77px;width:79px;height:23px;border:1px solid #bbb;font-size:7px;display:flex;align-items:center;justify-content:center;gap:5px}
</style>
</head>
<body>

<div class="abs brand"><span class="mark"></span>Harbora</div>
<div class="abs top-phone">
  <svg width="9" height="9" viewBox="0 0 24 24"><path fill="#1b3f6e" d="M6.6 10.8a15 15 0 0 0 6.6 6.6l2.2-2.2a1 1 0 0 1 1-.25 11.4 11.4 0 0 0 3.6.6 1 1 0 0 1 1 1V20a1 1 0 0 1-1 1A17 17 0 0 1 3 4a1 1 0 0 1 1-1h3.5a1 1 0 0 1 1 1c0 1.25.2 2.45.6 3.6a1 1 0 0 1-.25 1z"/></svg>
  (555) 201 - 4470
</div>
<nav class="abs nav">
  <span class="active">Home</span><span>About Us</span><span>Products and Services</span><span>Insurance Plans</span><span>Contact Us</span>
</nav>

<div class="abs hero" role="img" aria-label="Photo of a smiling family of four leaning on a white sofa"></div>
<div class="abs dots"><span class="on"></span><span></span><span></span><span></span></div>

<section class="abs welcome">
  <h1>Welcome to Harbora</h1>
  <p class="lead">Praesent tortor neque, lobortis nec congue eget, pharetra scelerisque tortor.</p>
  <p class="body">Harbora Insurance Group has joined with regional &amp; national insurance companies to provide quality products and superior service. We take the time to discuss options and coverages, not to just sell insurance products. We strive to educate you in the decision making process to become an informed consumer. We specialize in commercial business &amp; personal insurance. We are committed to providing personal attention to all your insurance needs.</p>
  <p class="body">At Harbora Insurance Group, we are independent insurance agents. As independent agents, we do not work for any one insurance company; we sell coverage from several different companies. This allows us to focus on providing you with the right amount of insurance and the right type of coverage for your unique needs.</p>
</section>

<section class="abs band left" role="img" aria-label="Business insurance background of a handshake, tinted blue">
  <h2 style="left:82px">Business Insurance</h2>
  <ul style="left:83px">
    <li>Bond</li><li>Builders Risk</li><li>Business Owners Policy (BOP)</li><li>Commercial Auto</li><li>Crime</li><li>Crop / Hail</li><li>Difference in Conditions</li><li>Directors and Officers (D&amp;O)</li><li>Employment Practices Liability</li><li>Errors &amp; Omissions (E&amp;O)</li><li>Equipment Breakdown</li>
  </ul>
  <ul style="left:218px">
    <li>Garage</li><li>General Liability</li><li>Inland Marine</li><li>Liquor Liability</li><li>Medical Malpractice</li><li>Owners and Contractors Protective Liability (OCP)</li><li>Professional Liability</li><li>Property</li><li>Truckers</li><li>Umbrella</li>
  </ul>
</section>
<section class="abs band right" role="img" aria-label="Personal insurance background of a couple, tinted blue">
  <h2 style="left:43px">Personal Insurance</h2>
  <ul style="left:44px">
    <li>Auto</li><li>Boat &amp; Marine</li><li>Collector Car</li><li>Condo</li><li>Flood</li><li>High Net Worth</li><li>Homeowners</li><li>Rental and Investment Property</li><li>Mobile Home</li><li>Motor Home</li><li>Motorcycle</li>
  </ul>
  <ul style="left:168px">
    <li>Personal Umbrella</li><li>Recreational Vehicles</li><li>Renters</li><li>Travel</li><li>Valuable Items</li>
  </ul>
</section>

<section class="abs quote">
  <h2>Get a Quick Quote</h2>
  <div class="field" style="left:90px;top:56px;width:130px">Name</div>
  <div class="field" style="left:236px;top:56px;width:130px">Email</div>
  <div class="field" style="left:381px;top:56px;width:130px">Phone</div>
  <div class="field" style="left:527px;top:56px;width:130px">Insurance type<span class="arrow">▲▼</span></div>
  <div class="field" style="left:90px;top:96px;width:567px">Messages</div>
  <div class="abs btn-next">NEXT STEP</div>
</section>

<div class="abs map" role="img" aria-label="Light grey world map"></div>

<footer class="abs footer">
  <div class="info" style="left:83px">
    <svg width="7" height="10" viewBox="0 0 24 34"><path fill="#ddd" d="M12 0a12 12 0 0 0-12 12c0 9 12 22 12 22s12-13 12-22A12 12 0 0 0 12 0zm0 17a5 5 0 1 1 0-10 5 5 0 0 1 0 10z"/></svg>
    <span>1280 Coral Bay Avenue, Suite 210<br>Bayview, FL 30120</span>
  </div>
  <div class="info" style="left:220px;top:24px">
    <svg width="8" height="8" viewBox="0 0 24 24"><path fill="#ddd" d="M6.6 10.8a15 15 0 0 0 6.6 6.6l2.2-2.2a1 1 0 0 1 1-.25 11.4 11.4 0 0 0 3.6.6 1 1 0 0 1 1 1V20a1 1 0 0 1-1 1A17 17 0 0 1 3 4a1 1 0 0 1 1-1h3.5a1 1 0 0 1 1 1c0 1.25.2 2.45.6 3.6a1 1 0 0 1-.25 1z"/></svg>
    <span>Phone : (555) 318 7720</span>
  </div>
  <div class="info" style="left:339px;top:24px">
    <svg width="8" height="8" viewBox="0 0 10 10"><rect x="1" y="3" width="8" height="5" fill="#ddd"/><rect x="3" y="1" width="4" height="2" fill="#ddd"/></svg>
    <span>Fax : (555) 318 7720</span>
  </div>
  <div class="info" style="left:444px;top:24px">
    <svg width="10" height="8" viewBox="0 0 10 8"><rect width="10" height="8" fill="#ddd"/><path d="M0 0l5 4 5-4" fill="none" stroke="#3b3b3b"/></svg>
    <span>Email:&nbsp; info@harbora.com</span>
  </div>
  <div class="social"><span></span><span></span><span></span><span></span></div>
  <div class="rule"></div>
  <div class="links">Home &nbsp;|&nbsp; About Us &nbsp;|&nbsp; Products and Services &nbsp;|&nbsp; Insurance Plans &nbsp;|&nbsp; Contact Us</div>
  <div class="copy">Copyright © 2016 Harbora. &nbsp;All rights reserved.</div>
  <div class="btn-contact">
    <svg width="8" height="6" viewBox="0 0 10 8"><rect x=".5" y=".5" width="9" height="7" fill="none" stroke="#ddd"/><path d="M.5 .5l4.5 4 4.5-4" fill="none" stroke="#ddd"/></svg>
    Contact Today
  </div>
</footer>

</body>
</html>
```